Bramblewood Card Company Business Cards

We are a trading card store with Glimmorax, sports and other TCG cards, we need a business card design that encompasses a clean cut, modern style with a retro flare. website is bramblewoodcardco.com for reference. Can utilize a comic book era feel or a more modern outdoor feel to utilize the "Pacific Northwest" elements of tress, mountains, etc.

Industry/Entity Type

Trading cards and collectibles

Contact Information for Business Card

business name, email address, phone number, name, owner job title

Font styles to use
Sans Serif

```html
<!DOCTYPE html>
<html lang="en">
<head>
<meta charset="utf-8">
<title>Bramblewood Card Company – Business Card</title>
<link rel="stylesheet" href="https://fonts.googleapis.com/css2?family=Montserrat:wght@400;500;700&display=swap">
<style>
  :root {
    --backdrop: #d3d6d7;
    --paper: #f7f7f7;
    --teal: #1b9cc0;
    --charcoal: #3f3f42;
    --ink: #3a3a3a;
    --rule: #b8b8b8;
  }
  * { box-sizing: border-box; margin: 0; padding: 0; }
  html, body {
    width: 1200px; height: 829px; overflow: hidden;
    background: var(--backdrop);
    font-family: "Montserrat", sans-serif;
  }
  .sheet {
    position: relative; width: 1200px; height: 829px;
    display: flex; align-items: center; justify-content: center; gap: 60px;
  }
  .card {
    position: relative; width: 510px; height: 292px;
    background: var(--paper);
    border-bottom: 5px solid var(--teal);
    box-shadow: 0 10px 24px rgba(0,0,0,.18);
  }
  /* front side */
  .identity {
    position: absolute; right: 292px; top: 92px; text-align: right;
  }
  .identity__name {
    color: var(--teal); font-weight: 700; font-size: 21px; letter-spacing: 1px;
    text-transform: uppercase;
  }
  .identity__role { color: var(--ink); font-size: 13px; margin-top: 3px; }
  .divider {
    position: absolute; left: 236px; top: 90px; width: 1px; height: 70px;
    background: var(--rule);
  }
  .contact {
    position: absolute; left: 254px; top: 92px; list-style: none;
  }
  .contact__item {
    display: flex; align-items: center; gap: 8px;
    color: var(--ink); font-size: 12.5px; line-height: 23px;
  }
  .contact__icon { width: 11px; height: 11px; fill: var(--teal); flex: none; }
  .address {
    position: absolute; left: 0; right: 0; top: 206px; text-align: center;
    color: var(--ink); font-size: 12.5px; letter-spacing: .3px;
  }
  /* back side */
  .card--back { display: flex; align-items: center; justify-content: center; gap: 12px; }
  .brand__mark { width: 18px; height: 18px; background: var(--teal); }
  .brand__name {
    color: var(--charcoal); font-weight: 700; font-size: 22px; letter-spacing: 1.5px;
    text-transform: uppercase;
  }
</style>
</head>
<body>
<main class="sheet">
  <section class="card card--front" aria-label="Business card front">
    <div class="identity">
      <p class="identity__name">Dorian Hale</p>
      <p class="identity__role">CEO/Founder</p>
    </div>
    <span class="divider"></span>
    <ul class="contact">
      <li class="contact__item">
        <svg class="contact__icon" viewBox="0 0 24 24"><path d="M6.6 10.8a15.1 15.1 0 0 0 6.6 6.6l2.2-2.2a1 1 0 0 1 1-.25 11.4 11.4 0 0 0 3.6.57 1 1 0 0 1 1 1V20a1 1 0 0 1-1 1A17 17 0 0 1 3 4a1 1 0 0 1 1-1h3.5a1 1 0 0 1 1 1c0 1.25.2 2.45.57 3.6a1 1 0 0 1-.25 1z"/></svg>
        (123) 456 7890
      </li>
      <li class="contact__item">
        <svg class="contact__icon" viewBox="0 0 24 24"><path d="M2 5h20v14H2z M2 5l10 8 10-8" /><path d="M2 5l10 8 10-8" fill="#fff" stroke="#fff" stroke-width="1.5"/></svg>
        info@bramblewoodcardco.com
      </li>
      <li class="contact__item">
        <svg class="contact__icon" viewBox="0 0 24 24"><circle cx="12" cy="12" r="10"/><path d="M2 12h20M12 2c3 3 3 17 0 20M12 2c-3 3-3 17 0 20" stroke="#fff" stroke-width="1.4" fill="none"/></svg>
        www.bramblewoodcardco.com
      </li>
    </ul>
    <p class="address">P.O. Box 2145 Street Country Name AB 8542</p>
  </section>

  <section class="card card--back" aria-label="Business card back">
    <span class="brand__mark"></span>
    <span class="brand__name">Bramblewood Card Company</span>
  </section>
</main>
</body>
</html>
```